Help Give House Painter “Fresh” Website Makeover!

A residential and commercial painting company based in Albuquerque, NM, USA needs a fresh, new, fun, and playful--yet, simple, elegant and professional--website made.

Here is a link to their existing site:

http://corvelcoatings.example/

We want to keep a similar site structure., So the navigation layout will stay the same. However, the video is too small, is too far over in the sidebar, and the overall design is amateur at best. We want something bright, colorful and bold!

We will need a space for the Video above the fold, and there needs to be space in the design for Testimonials, Specials and Images. It’s also very important to have the Pellham Roster awards that you see on his current website.

Please also include somewhere in the Design icons for YouTube, Facebook, Google+ and LinkedIn.

Here are some examples to look at to get your creative juices flowing!

http://brightloombrush.example/

http://www.tkvr.example/

http://www.marblow-tennick.example/

http://www.quarrypages.example/painting-company-niche-website/

http://www.brisklayoutdepot.example/website-templates/painting-company-website-template-53817.html

We have accounts at both lumavault.example and pixaroo.example. If you use placeholder images from there, that's fine. We can buy the images when and if your design is selected.

Target Market(s)

The audience is the average middle class homeowner to higher upper class. This should appeal to families, couples, and singles who own a home.

Industry/Entity Type

Residential

Font styles to use
Sans Serif

Requirements
Must have
• - - Lots of color! It's a site about painting homes. People like a variety of colors. Bring out your inner artist, and get bold with your colors!

- - A video place holder. As you can see, there is a video on the existing site, but it's small and hidden. Make it big and put it top left, or in the center.

- -Detailed and organized PSD structure. We're going to turn your design into a website, and to make that work soothly, we ask that you organize you PSD well: name your layers, keep things separated, group and ungroup as necessary, etc.

- A sidebar that goes down the right side of an interior page. We need a homepage, and also one [1] interior page template. We don't need you to make a design for each page. Just the homepage, followed by a simple interior page design that requires only the header/navigation, and a sidebar down the right side.
Should not have
• - Coding. This is a design project only.

```html
<!DOCTYPE html>
<html lang="en">
<head>
<meta charset="utf-8">
<title>Corvel Coatings – Residential &amp; Commercial Painting</title>
<link rel="stylesheet" href="https://fonts.googleapis.com/css2?family=Lato:ital,wght@0,400;0,700;0,900;1,400;1,700;1,900&family=Oswald:wght@400;500&family=Open+Sans:wght@400;600&display=swap">
<style>
:root{
  --blue:#1a5fb4;
  --blue-dark:#1446a0;
  --blue-nav-top:#2f8fe0;
  --blue-nav-bot:#0f5fb8;
  --red:#e0242c;
  --red-panel:#c4262d;
  --gold:#f2a81d;
  --gold-dark:#d98c0c;
  --navy:#1e2c4c;
  --navy-deep:#0c2a66;
  --white:#fff;
  --ink:#444;
  --orange:#f26b0f;
  --card-blue:#2a7fc0;
  --green:#36a111;
  --card-red:#e31b23;
  --card-gold:#cf8a0b;
}
*{box-sizing:border-box;margin:0;padding:0}
html,body{width:801px;height:1200px;overflow:hidden}
body{position:relative;background:var(--white);font-family:"Lato",sans-serif;color:var(--ink)}
.abs{position:absolute}

/* header */
.site-header{position:absolute;left:0;top:0;width:801px;height:80px;background:var(--white)}
.brand{position:absolute;left:88px;top:16px;display:flex;align-items:center;gap:8px}
.brand-dot{width:44px;height:44px;border-radius:50%;background:var(--blue)}
.brand-name{font:900 24px/1 "Lato",sans-serif;color:var(--blue);letter-spacing:.3px}
.brand-tag{position:absolute;left:170px;top:48px;font:700 10px/1 "Lato",sans-serif;color:#555;letter-spacing:1.2px}
.award{position:absolute;top:8px;width:100px;text-align:center}
.award svg{display:block;margin:0 auto}
.award span{display:block;margin-top:6px;font:700 8.5px/1 "Lato",sans-serif;color:#333}
.header-phone{position:absolute;left:598px;top:33px;display:flex;align-items:center;gap:6px;font:400 16px/1 "Lato",sans-serif;color:var(--red)}

/* nav */
.main-nav{position:absolute;left:0;top:80px;width:801px;height:32px;background:linear-gradient(var(--blue-nav-top),var(--blue-nav-bot))}
.main-nav a{position:absolute;top:11px;font:700 10px/1 "Lato",sans-serif;color:var(--white);text-decoration:none;text-transform:uppercase}
.main-nav a.current{border-bottom:2px solid var(--white);padding-bottom:6px}

/* hero */
.hero-bg{position:absolute;left:0;top:112px;width:801px;height:316px;background:linear-gradient(90deg,#d4702a 0%,#e08a45 10%,#e9a064 50%,#e58a3a 80%,#c96a26 100%)}
.video{position:absolute;left:87px;top:112px;width:427px;height:240px;background:linear-gradient(90deg,#c8581a 0%,#e07c35 40%,#d9d4cc 55%,#eeeeee 100%)}
.video-brand{position:absolute;left:0;top:32px;width:220px;text-align:center;font:500 14px/1 "Oswald",sans-serif;color:var(--blue-dark)}
.video-title{position:absolute;left:0;top:54px;width:220px;text-align:center;font:400 16px/20px "Oswald",sans-serif;color:var(--white)}
.play{position:absolute;left:196px;top:100px}
.controls{position:absolute;left:0;top:222px;width:427px;height:18px;background:linear-gradient(#3a3a3a,#161616)}
.controls .bar{position:absolute;left:34px;top:7px;width:126px;height:4px;border-radius:2px;background:#888}
.controls .bar i{position:absolute;left:0;top:0;width:30px;height:4px;background:#ccc;border-radius:2px}
.controls .time{position:absolute;left:166px;top:5px;font:400 7px/1 "Lato",sans-serif;color:#ddd}
.ctl{position:absolute;top:4px;width:14px;height:10px;border-radius:2px;background:#4f6f9f}
.hero-strip{position:absolute;left:87px;top:352px;width:427px;height:76px;background:var(--blue-dark)}
.hero-strip p{position:absolute;left:14px;top:15px;font:400 11.5px/15px "Oswald",sans-serif;color:var(--white)}
.hero-strip b{color:var(--gold);font-weight:400}
.chamber-badge{position:absolute;left:352px;top:16px;width:62px;height:42px;background:#0a1d4a;border:1.5px solid var(--white)}

/* estimate form */
.estimate{position:absolute;left:514px;top:112px;width:200px;height:316px;background:var(--red-panel)}
.estimate-head{height:33px;background:linear-gradient(var(--gold),var(--gold-dark));text-align:center;font:700 13.5px/33px "Lato",sans-serif;color:var(--white);letter-spacing:.3px}
.estimate h2{margin-top:26px;text-align:center;font:700 12.5px/1 "Lato",sans-serif;color:var(--white)}
.estimate .intro{margin:4px 6px 0;text-align:center;font:400 8px/10.5px "Open Sans",sans-serif;letter-spacing:-.1px;color:var(--white)}
.field{position:absolute;left:11px;width:176px;height:16px;background:var(--white);border-radius:2px;font:400 8px/16px "Open Sans",sans-serif;color:#444;padding-left:6px}
.field.area{height:37px;line-height:1;padding-top:5px}
.cap-label{position:absolute;left:11px;top:241px;font:400 8px/1 "Open Sans",sans-serif;color:var(--white)}
.submit{position:absolute;left:12px;top:277px;width:86px;height:22px;border-radius:3px;background:linear-gradient(#f5b733,var(--gold-dark));font:700 11px/22px "Lato",sans-serif;color:var(--white);text-align:center}

/* main */
.content-bg{position:absolute;left:0;top:428px;width:801px;height:582px;background:linear-gradient(#c5dcf1,#dcebf8 60%,#cfe3f5)}
.welcome{position:absolute;left:88px;top:450px;width:411px;height:230px;background:var(--white);border:1px solid #b9cfe4;border-radius:6px;padding:15px 13px}
.welcome h1{font:600 12.5px/1 "Open Sans",sans-serif;color:var(--blue-dark)}
.welcome h1 span{color:var(--red)}
.welcome p{margin-top:5px;font:400 9.2px/14px "Open Sans",sans-serif;letter-spacing:-.05px;color:#555;text-align:justify}
.btn-blue{position:absolute;left:13px;top:192px;width:64px;height:22px;background:#1a8fd8;border-radius:2px;font:700 9px/22px "Lato",sans-serif;color:var(--white);text-align:center}

.service{position:absolute;width:132px;height:94px;border-radius:5px 5px 0 0;text-align:center;color:var(--white)}
.service h3{margin-top:40px;font:700 9.5px/1 "Lato",sans-serif;text-transform:uppercase}
.service p{margin-top:4px;font:700 8px/11px "Lato",sans-serif}
.service .more{position:absolute;left:38px;bottom:-8px;width:56px;height:16px;background:#2b2b2b;border-radius:2px;font:700 8.5px/16px "Lato",sans-serif;color:var(--white)}
.thumb{position:absolute;width:64px;height:64px;border-radius:50%;border:3px solid var(--white);box-shadow:0 0 0 1px #999}

/* sidebar */
.sidebar{position:absolute;left:514px;top:428px;width:200px;height:582px;background:var(--navy)}
.side-head{position:absolute;left:0;top:21px;width:200px;height:24px;background:linear-gradient(var(--gold),var(--gold-dark));padding:0 12px;font:700 12px/24px "Lato",sans-serif;color:var(--white)}
.side-head em{position:absolute;right:9px;top:0;font:italic 700 8.5px/24px "Lato",sans-serif;color:#3a2a0a}
.avatar{position:absolute;left:13px;width:58px;height:58px;border-radius:50%;border:3px solid var(--orange);background:linear-gradient(#7b8fa8,#5a6a80)}
.t-name{position:absolute;left:82px;font:700 9px/1 "Lato",sans-serif;color:var(--gold)}
.t-role{position:absolute;left:82px;font:400 8.5px/1 "Lato",sans-serif;color:var(--white)}
.quote{position:absolute;left:13px;width:174px;height:103px;background:var(--white);padding:5px 6px 0 8px;font:italic 400 8.8px/15px "Lato",sans-serif;color:#444}
.quote::before{content:"";position:absolute;left:44px;top:-8px;border:8px solid transparent;border-top:0;border-bottom-color:var(--white)}
.specials{position:absolute;left:0;top:460px;width:200px;height:94px;background:linear-gradient(90deg,#4a3a2a,#7a6a52 50%,#5a4a38)}
.specials p{position:absolute;left:0;top:22px;width:200px;text-align:center;font:italic 900 19px/24px "Lato",sans-serif;color:var(--white)}

/* footer */
.site-footer{position:absolute;left:0;top:1010px;width:801px;height:190px;background:var(--blue-dark)}
.quick{position:absolute;left:88px;top:0;width:168px;height:190px;background:#eef1f4}
.quick h4{height:27px;background:linear-gradient(var(--gold),var(--gold-dark));padding-left:13px;font:700 11px/27px "Lato",sans-serif;color:var(--white)}
.quick ul{list-style:none;margin-top:9px}
.quick li{position:relative;padding-left:34px;height:16.8px;font:700 8.5px/16.8px "Lato",sans-serif;color:#222}
.quick li::before{content:"";position:absolute;left:14px;top:6px;width:5px;height:5px;border-radius:50%;background:var(--blue)}
.f-title{position:absolute;font:700 11px/1 "Lato",sans-serif;color:var(--white)}
.news-input{position:absolute;left:282px;top:37px;width:209px;height:24px;background:var(--white);font:400 7.5px/24px "Lato",sans-serif;color:#888;padding-left:8px}
.news-btn{position:absolute;left:496px;top:37px;width:55px;height:24px;background:var(--red);font:400 10px/24px "Lato",sans-serif;color:var(--white);text-align:center}
.social{position:absolute;top:37px;width:20px;height:20px;border-radius:50%}
.rule{position:absolute;background:#3b68b5}
.f-text{position:absolute;font:400 8.5px/14px "Lato",sans-serif;color:var(--white)}
.bbb{position:absolute;left:600px;top:90px;width:115px;height:46px;background:var(--white);border-radius:5px}
.bbb i{position:absolute;left:17px;top:8px;width:81px;height:30px;background:#0d5a86;border-radius:3px}
.copy{position:absolute;left:256px;top:168px;width:458px;text-align:center;font:700 8.5px/1 "Lato",sans-serif;color:var(--white)}
</style>
</head>
<body>

<header class="site-header">
  <div class="brand"><span class="brand-dot"></span><span class="brand-name">CORVEL COATINGS</span></div>
  <div class="brand-tag">NOT JUST ANOTHER PAINTER</div>
  <div class="award" style="left:381px">
    <svg width="32" height="46" viewBox="0 0 32 46" role="img" aria-label="Service award badge"><path d="M2 2h28v26c0 9-7 14-14 16C9 42 2 37 2 28z" fill="#e6b325" stroke="#a67a10" stroke-width="1.5"/></svg>
    <span>EXTERIOR PAINTING</span>
  </div>
  <div class="award" style="left:472px">
    <svg width="32" height="46" viewBox="0 0 32 46" role="img" aria-label="Service award badge"><path d="M2 2h28v26c0 9-7 14-14 16C9 42 2 37 2 28z" fill="#e6b325" stroke="#a67a10" stroke-width="1.5"/></svg>
    <span>INTERIOR PAINTING</span>
  </div>
  <div class="header-phone">
    <svg width="17" height="17" viewBox="0 0 17 17"><circle cx="8.5" cy="8.5" r="7.5" fill="none" stroke="#1a5fb4" stroke-width="1.4"/><path d="M6 4.5l1.6 2-1 1c.5 1.2 1.3 2 2.5 2.6l1-1 2 1.5-.9 1.6c-3-.3-5.5-2.8-5.9-5.9z" fill="#1a5fb4"/></svg>
    <span>123 456 7890</span>
  </div>
</header>

<nav class="main-nav">
  <a class="current" style="left:88px">Home</a>
  <a style="left:128px">About Us</a>
  <a style="left:190px">Residential Painting</a>
  <a style="left:312px">Commercial Painting</a>
  <a style="left:438px">FAQ</a>
  <a style="left:472px">Specials</a>
  <a style="left:530px">Blog</a>
  <a style="left:571px">Testimonials</a>
  <a style="left:654px">Contact Us</a>
</nav>

<div class="hero-bg" role="img" aria-label="Freshly painted orange interior wall with wooden floor"></div>

<section class="video" role="img" aria-label="Video still: bedroom half painted orange, half white">
  <div class="video-brand">CORVEL COATINGS</div>
  <div class="video-title">RESIDENTIAL &amp; COMMERCIAL<br>PAINTING COMPANY</div>
  <svg class="play" width="34" height="22" viewBox="0 0 34 22"><rect width="34" height="22" rx="5" fill="#e0242c"/><path d="M13 6l9 5-9 5z" fill="#fff"/></svg>
  <div class="controls">
    <span class="ctl" style="left:6px"></span>
    <span class="bar"><i></i></span>
    <span class="time">1:47 / 12:35</span>
    <span class="ctl" style="left:366px"></span>
    <span class="ctl" style="left:386px"></span>
    <span class="ctl" style="left:406px"></span>
  </div>
</section>

<section class="hero-strip">
  <p>Need Painting In The Albuquerque Area?<br>Call Dale Today For Your FREE Painting Estimate! <b>555-0148</b><br>Licensed - Bonded - Insured</p>
  <span class="chamber-badge" role="img" aria-label="Chamber of commerce membership badge"></span>
</section>

<aside class="estimate">
  <div class="estimate-head">SCHEDULE FREE ESTIMATE</div>
  <h2>How to Schedule an Estimae</h2>
  <p class="intro">Requesting an estimate online is very simple and easy. Fill out the Form below and we will send you a rough quote to your email. We may also call you if we have any more questions.</p>
  <div class="field" style="top:131px">Name:</div>
  <div class="field" style="top:153px">Email:</div>
  <div class="field" style="top:175px">Phone:</div>
  <div class="field area" style="top:198px">Decribe what needs to be done.</div>
  <div class="cap-label">Please type the following</div>
  <div class="field" style="top:254px">ac2gH</div>
  <div class="submit">Submit Now</div>
</aside>

<div class="content-bg"></div>

<article class="welcome">
  <h1>Welcome To CORVEL <span>COATINGS</span></h1>
  <p>Corvel Coatings does jobs as small as a bathroom up to large commercial projects right here in Albuquerque and Rio Rancho. Extensive as an entire apartment exterior, to a kitchen and all home interior, no job is too big or too small for Corvel Coatings of Albuquerque. Corvel Coatings is staffed with the best painters for the highest quality paint jobs. Corvel Coatings is not a community’s average house painter staffing company, but this painting company is staffed with professional painters that pride themselves on successfully completing every job.</p>
  <p>Dale Prescott, owner of Corvel Coatings, Inc., started painting in 1975 during high school. He continued painting through college where he earned a Bachelor of Science degree from Westbrook University in 1984. Dale opened his first company in 1984.</p>
  <div class="btn-blue">Read More</div>
</article>

<div class="service" style="left:87px;top:735px;background:var(--orange)"><h3>Commercial Painting</h3><p>Lorem ipsum dolor sit amet,<br>consectetuer adipiscing</p><div class="more">Read more</div></div>
<div class="service" style="left:228px;top:735px;background:var(--card-blue)"><h3>Residential Painting</h3><p>Lorem ipsum dolor sit amet,<br>consectetuer adipiscing</p><div class="more">Read more</div></div>
<div class="service" style="left:369px;top:735px;background:var(--green)"><h3 style="margin-top:38px">Stucco Coatings</h3><p>Lorem ipsum dolor sit amet,<br>consectetuer adipiscing</p><div class="more">Read more</div></div>
<div class="service" style="left:87px;top:888px;background:var(--navy-deep)"><h3>Cabinets</h3><p>Lorem ipsum dolor sit amet,<br>consectetuer adipiscing</p><div class="more">Read more</div></div>
<div class="service" style="left:228px;top:888px;background:var(--card-red)"><h3>Interior/ Exterior</h3><p>Lorem ipsum dolor sit amet,<br>consectetuer adipiscing</p><div class="more">Read more</div></div>
<div class="service" style="left:369px;top:888px;background:var(--card-gold)"><h3>Dry Wall Texture Repair</h3><p>Lorem ipsum dolor sit amet,<br>consectetuer adipiscing</p><div class="more">Read more</div></div>

<span class="thumb" style="left:121px;top:700px;background:linear-gradient(#e8e8e8,#a9a9a9)" role="img" aria-label="Commercial office interior"></span>
<span class="thumb" style="left:262px;top:700px;background:linear-gradient(#8fb3d8,#c9b59a)" role="img" aria-label="Painted house exterior"></span>
<span class="thumb" style="left:403px;top:700px;background:linear-gradient(#8a5a44,#c9a98c)" role="img" aria-label="Stucco wall texture"></span>
<span class="thumb" style="left:121px;top:855px;background:linear-gradient(#d9d4cc,#8a8175)" role="img" aria-label="Kitchen cabinets"></span>
<span class="thumb" style="left:262px;top:855px;background:linear-gradient(#3a2a22,#d98a3a)" role="img" aria-label="Lit home at dusk"></span>
<span class="thumb" style="left:403px;top:855px;background:linear-gradient(#c7d7e4,#b89a6a)" role="img" aria-label="Drywall room repair"></span>

<aside class="sidebar">
  <div class="side-head">Testimonials<em>View All</em></div>
  <span class="avatar" style="top:55px" role="img" aria-label="Customer portrait"></span>
  <span class="t-name" style="top:73px">Marco Teller</span>
  <span class="t-role" style="top:86px">Lorem Ipsum</span>
  <div class="quote" style="top:122px">“ Ut wisi enim ad minim veniam, quism nostrli erci tation ullamcorper suscipitop lobortis commodo consequat Ut wisi enim ad minim veniam, quism nostrli erci tation ullamcorper suscipitop lobortis commodo consequat. ”</div>
  <span class="avatar" style="top:237px" role="img" aria-label="Customer portrait"></span>
  <span class="t-name" style="top:255px">Marco Teller</span>
  <span class="t-role" style="top:268px">Lorem Ipsum</span>
  <div class="quote" style="top:305px">“ Ut wisi enim ad minim veniam, quism nostrli erci tation ullamcorper suscipitop lobortis commodo consequat Ut wisi enim ad minim veniam, quism nostrli erci tation ullamcorper suscipitop lobortis commodo consequat. ”</div>
  <div class="specials" role="img" aria-label="Freshly painted living room"><p>Check Out<br>Our Specials!</p></div>
</aside>

<footer class="site-footer">
  <nav class="quick">
    <h4>Quick Links</h4>
    <ul>
      <li>HOME</li><li>ABOUT US</li><li>RESIDENTIAL PAINTING</li><li>COMMERCIAL PAINTING</li><li>FAQ</li><li>SPECIALS</li><li>BLOG</li><li>TESTIMONIALS</li><li>CONTACT US</li>
    </ul>
  </nav>
  <div class="f-title" style="left:283px;top:16px">Sign up for Newsletter</div>
  <div class="news-input">Enter Your Email</div>
  <div class="news-btn">SUBMIT</div>
  <div class="rule" style="left:576px;top:18px;width:1px;height:44px"></div>
  <div class="f-title" style="left:601px;top:16px">Follow Us On</div>
  <span class="social" style="left:600px;background:#3a6aa8"></span>
  <span class="social" style="left:627px;background:#3a7ab8"></span>
  <span class="social" style="left:654px;background:#2f5f98"></span>
  <span class="social" style="left:681px;background:#c0392b"></span>
  <div class="rule" style="left:282px;top:77px;width:432px;height:1px"></div>
  <svg class="abs" style="left:281px;top:95px" width="11" height="15" viewBox="0 0 11 15"><path d="M5.5 0A5.5 5.5 0 0 0 0 5.5C0 9.5 5.5 15 5.5 15S11 9.5 11 5.5A5.5 5.5 0 0 0 5.5 0zm0 7.5a2 2 0 1 1 0-4 2 2 0 0 1 0 4z" fill="#fff"/></svg>
  <div class="f-text" style="left:300px;top:94px">Corvel Coatings Inc.<br>4100 Ridgeway Lane Northeast,<br>Albuquerque, NM 87109</div>
  <svg class="abs" style="left:471px;top:96px" width="8" height="12" viewBox="0 0 8 12"><rect x=".5" y=".5" width="7" height="11" rx="1.5" fill="none" stroke="#fff"/><circle cx="4" cy="9.5" r=".8" fill="#fff"/></svg>
  <div class="f-text" style="left:488px;top:94px;font-size:10px">505-555-0192</div>
  <svg class="abs" style="left:436px;top:120px" width="11" height="8" viewBox="0 0 11 8"><rect x=".5" y=".5" width="10" height="7" fill="none" stroke="#fff"/><path d="M.5.5l5 4 5-4" fill="none" stroke="#fff"/></svg>
  <div class="f-text" style="left:454px;top:117px">info@corvelcoatings.example</div>
  <div class="rule" style="left:576px;top:88px;width:1px;height:44px"></div>
  <div class="bbb" role="img" aria-label="Accreditation badge"><i></i></div>
  <div class="rule" style="left:282px;top:147px;width:432px;height:1px"></div>
  <div class="copy">© 2015 CORVEL COATINGS. All Rights Reserved.</div>
</footer>

</body>
</html>
```